Business Card for a mobile physiotherapy company

I need a layout for a business card for a mobile physiotherapy company.
Slogan is "Mobile Physiotherapy - Your Road To Recovery"
Phone number is 867-555-0142
Email VardenTherapy@postnest.ca (subject to change with website)
Website www.VardenTherapy.ca
My name and credentials: Luke Varden Luke Varden, BSc(kin), MPT, CAFCI, IMS
Information maybe included: Direct Billing, Services including Physiotherapy, IMS, acupuncture
Maybe include facebook and instagram logos
One side with the logo clean and sharp
Other side with details, try not to look too busy, keep everything concise

```html
<!DOCTYPE html>
<html lang="en">
<head>
<meta charset="utf-8">
<title>Varden Therapy – Business Card</title>
<link rel="stylesheet" href="https://fonts.googleapis.com/css2?family=Lato:wght@400;700&family=Libre+Baskerville:wght@700&display=swap">
<style>
  :root {
    --backdrop: #3a3431;
    --card: #0d0d0e;
    --card-edge: #1b1b1c;
    --teal: #1f6e62;
    --blue: #3d5f99;
    --text: #e9e9e9;
    --muted: #bdbdbd;
    --silver: #d6d6d6;
    --rule: #4a4a4a;
  }
  * { box-sizing: border-box; margin: 0; padding: 0; }
  html, body { width: 1200px; height: 844px; overflow: hidden; }
  body {
    background: var(--backdrop);
    font-family: "Lato", sans-serif;
    color: var(--text);
    position: relative;
  }
  .card {
    position: absolute;
    top: 279px;
    width: 510px;
    height: 292px;
    background: var(--card);
    border: 1px solid var(--card-edge);
    box-shadow: 0 18px 40px rgba(0,0,0,.45);
  }
  .card--details { left: 60px; }
  .card--logo { left: 630px; }

  /* Details side */
  .brand-block {
    position: absolute;
    left: 0; top: 0;
    width: 250px; height: 100%;
    display: flex; flex-direction: column;
    align-items: center; justify-content: center;
    gap: 10px;
  }
  .brand-mark {
    width: 14px; height: 14px;
    background: var(--teal);
  }
  .brand-name {
    font-family: "Lato", sans-serif;
    font-weight: 700;
    font-size: 30px;
    letter-spacing: 4px;
    color: var(--teal);
    text-transform: uppercase;
    text-align: center;
    line-height: 1.15;
  }
  .divider {
    position: absolute;
    left: 262px; top: 60px;
    width: 1px; height: 172px;
    background: var(--rule);
  }
  .contact-block {
    position: absolute;
    left: 282px; top: 62px;
    right: 16px;
  }
  .person-name {
    font-family: "Libre Baskerville", serif;
    font-weight: 700;
    font-size: 17px;
    color: var(--teal);
    text-transform: uppercase;
    letter-spacing: .5px;
  }
  .credentials {
    font-family: "Libre Baskerville", serif;
    font-size: 11px;
    color: var(--muted);
    margin-top: 4px;
    letter-spacing: .4px;
  }
  .contact-list { list-style: none; margin-top: 10px; }
  .contact-list li {
    display: flex; align-items: center; gap: 7px;
    font-size: 14px; line-height: 21px;
    color: var(--text);
  }
  .contact-list svg { width: 11px; height: 11px; flex: none; fill: var(--muted); }
  .services {
    margin-top: 14px;
    font-size: 14.5px;
    line-height: 21px;
    color: var(--text);
  }

  /* Logo side */
  .logo-stack {
    position: absolute;
    left: 0; right: 0; top: 62px;
    display: flex; flex-direction: column; align-items: center;
    gap: 10px;
  }
  .logo-mark { width: 16px; height: 16px; background: var(--silver); }
  .logo-name {
    font-family: "Lato", sans-serif;
    font-weight: 700;
    font-size: 34px;
    letter-spacing: 6px;
    color: var(--silver);
    text-transform: uppercase;
    text-align: center;
    line-height: 1.15;
  }
  .social-dots { display: flex; gap: 6px; margin-top: 4px; }
  .social-dots span {
    width: 14px; height: 14px; border-radius: 50%;
    background: var(--text);
  }
  .tagline-rule {
    position: absolute;
    left: 40px; right: 40px; top: 232px;
    height: 1px; background: var(--rule);
  }
  .tagline {
    position: absolute;
    left: 0; right: 0; top: 244px;
    text-align: center;
    font-size: 12px;
    letter-spacing: .6px;
    color: var(--text);
    text-transform: uppercase;
  }
</style>
</head>
<body>

<section class="card card--details" aria-label="Business card, contact side">
  <div class="brand-block">
    <span class="brand-mark"></span>
    <div class="brand-name">Varden<br>Therapy</div>
  </div>
  <div class="divider"></div>
  <div class="contact-block">
    <h1 class="person-name">Luke Varden</h1>
    <p class="credentials">BSC(KIN), MPT, CAFCI, IMS</p>
    <ul class="contact-list">
      <li>
        <svg viewBox="0 0 24 24" aria-hidden="true"><path d="M6.6 10.8a15.1 15.1 0 0 0 6.6 6.6l2.2-2.2c.3-.3.7-.4 1-.2 1.1.4 2.3.6 3.6.6.6 0 1 .4 1 1V20c0 .6-.4 1-1 1A17 17 0 0 1 3 4c0-.6.4-1 1-1h3.5c.6 0 1 .4 1 1 0 1.3.2 2.5.6 3.6.1.3 0 .7-.2 1z"/></svg>
        867-555-0142
      </li>
      <li>
        <svg viewBox="0 0 24 24" aria-hidden="true"><path d="M2 5h20v14H2z M2 5l10 8 10-8" fill="none" stroke="#bdbdbd" stroke-width="2.4"/></svg>
        VardenTherapy@postnest.ca
      </li>
      <li>
        <svg viewBox="0 0 24 24" aria-hidden="true"><circle cx="12" cy="12" r="10"/></svg>
        www.VardenTherapy.ca
      </li>
    </ul>
    <p class="services">Direct Billing| Physiotherapy<br>IMS | acupuncture</p>
  </div>
</section>

<section class="card card--logo" aria-label="Business card, logo side">
  <div class="logo-stack">
    <span class="logo-mark"></span>
    <div class="logo-name">Varden<br>Therapy</div>
    <div class="social-dots" aria-hidden="true"><span></span><span></span></div>
  </div>
  <div class="tagline-rule"></div>
  <p class="tagline">Mobile Physiotherapy - Your Road to Recovery</p>
</section>

</body>
</html>
```